Marlowe Group needs a business card

I would like the card to be simple but modern and elegant.
I like black and white.
or black and gold.
we are a private finance lender and also are involved in property and property developments.

please look at the business card photos i provided i would like M.G only one one side and all the other details on the other side use fonts that tie in with my theme.

Industry/Entity Type

Finance

Contact Information for Business Card

Marlowe Group (M.G) Daniel Marlowe M: 0413586207 E: danmarl@inboxmail.test

Font styles to use
Other font styles liked:
• Use fonts that would reflect our business

Colors
000000
ffffff

Requirements
Must have
• one side of details
• other side has either M.G or Marlowe Group like in the photos provided

```html
<!DOCTYPE html>
<html lang="en">
<head>
<meta charset="utf-8">
<title>Marlowe Group — Business Card</title>
<link rel="stylesheet" href="https://fonts.googleapis.com/css2?family=Linden+Hill&display=swap">
<style>
  :root {
    --page: #ffffff;
    --card-black: #000000;
    --gold: #d4b825;
    --olive-dark: #1f1b0c;
    --olive-mid: #3a3418;
    --coin-light: #f2d35a;
    --coin-deep: #a8821c;
  }
  html, body {
    margin: 0;
    padding: 0;
    width: 927px;
    height: 1200px;
    overflow: hidden;
    background: var(--page);
  }
  .sheet {
    position: relative;
    width: 927px;
    height: 1200px;
    font-family: "Linden Hill", "Times New Roman", serif;
    color: var(--gold);
  }
  .card {
    position: absolute;
    overflow: hidden;
  }
  .card-front {
    left: 60px;
    top: 37px;
    width: 816px;
    height: 464px;
    background: var(--card-black);
    display: flex;
    align-items: center;
    justify-content: center;
  }
  .card-back {
    left: 54px;
    top: 708px;
    width: 822px;
    height: 470px;
  }
  .back-texture {
    position: absolute;
    inset: 0;
    background: radial-gradient(ellipse at 40% 45%, var(--olive-mid) 0%, var(--olive-dark) 100%);
  }
  .frame-outer, .frame-inner {
    position: absolute;
    border: 2px solid var(--gold);
    box-sizing: border-box;
  }
  .frame-outer { inset: 12px; }
  .frame-inner { inset: 18px; }
  .brand-name {
    position: relative;
    margin: 0;
    font-weight: 400;
    font-size: 84px;
    line-height: 1;
    letter-spacing: 1px;
  }
  .company-name {
    position: absolute;
    left: 0;
    right: 0;
    top: 24px;
    margin: 0;
    text-align: center;
    font-weight: 400;
    font-size: 72px;
    line-height: 1;
  }
  .rule {
    position: absolute;
    left: 39px;
    width: 746px;
    height: 2px;
    background: var(--gold);
  }
  .rule-top { top: 114px; }
  .rule-bottom { top: 416px; }
  .coin {
    position: absolute;
    left: 65px;
    top: 164px;
    width: 186px;
    height: 186px;
  }
  .contact {
    position: absolute;
    right: 46px;
    top: 158px;
    margin: 0;
    text-align: right;
    font-style: normal;
    font-size: 42px;
    line-height: 68px;
  }
  .contact p { margin: 0; white-space: nowrap; }
</style>
</head>
<body>
<main class="sheet">
  <section class="card card-front" aria-label="Card front">
    <div class="frame-outer"></div>
    <div class="frame-inner"></div>
    <p class="brand-name">Marlowe Group</p>
  </section>

  <section class="card card-back" aria-label="Card back">
    <div class="back-texture" role="img" aria-label="Dark background of scattered gold coins"></div>
    <div class="frame-outer"></div>
    <div class="frame-inner"></div>
    <h1 class="company-name">Marlowe Group (M.G)</h1>
    <div class="rule rule-top"></div>
    <svg class="coin" viewBox="0 0 186 186" role="img" aria-label="Gold bullion coin">
      <defs>
        <radialGradient id="coinFill" cx="40%" cy="35%" r="70%">
          <stop offset="0%" stop-color="var(--coin-light)"/>
          <stop offset="100%" stop-color="var(--coin-deep)"/>
        </radialGradient>
      </defs>
      <circle cx="93" cy="93" r="92" fill="url(#coinFill)"/>
    </svg>
    <address class="contact">
      <p class="contact-name">Daniel Marlowe</p>
      <p class="contact-mobile">M: 0413586207</p>
      <p class="contact-email">E: danmarl@inboxmail.test</p>
    </address>
    <div class="rule rule-bottom"></div>
  </section>
</main>
</body>
</html>
```